Military and tactical gear supply company needs web design

We need a web design for a company called U.S. Torvane. We provide quality tactical equipment to military and law enforcement. This is an e-commerce business and we primarily market ourselves on social media. Our key products are backpacks, military-style belts, and tactical flashlights. The gear we sell is not yet widely known about, but is on par with the state-of-the-art products in this field. We want the website to convey the message of quality, durability, and reliability. We use the word "kinetic" because the customers in this field are very "action-oriented" and we would like that idea to be communicated in the web site as well. The primary demographic is men in their 20's-30's, so the web site should have a masculine feel to it. Attached is the logo and color scheme.

```html
<!DOCTYPE html>
<html lang="en">
<head>
<meta charset="utf-8">
<title>U.S. Torvane — Tactical Equipment</title>
<link rel="stylesheet" href="https://fonts.googleapis.com/css2?family=Roboto:ital,wght@0,400;0,500;0,700;1,400&family=Russo+One&display=swap">
<style>
:root{
  --red:#a50d1e;
  --navy:#1e4e6e;
  --grey:#b8b7b8;
  --dark:#1c1c1f;
  --ink:#222;
  --muted:#555;
  --gold:#d7a316;
  --green:#6d9a1f;
  --white:#fff;
}
*{margin:0;padding:0;box-sizing:border-box}
html,body{width:1200px;height:3805px;overflow:hidden}
body{font-family:"Roboto",sans-serif;color:var(--ink);background:var(--white);position:relative}
.abs{position:absolute}
.display{font-family:"Russo One",sans-serif}

/* header */
.topbar{top:0;left:0;width:1200px;height:76px;background:var(--white)}
.search{left:111px;top:18px;width:243px;height:40px;border:1px solid #ccc;border-radius:20px;box-shadow:0 1px 4px rgba(0,0,0,.15);font-size:13px;color:#777;padding:11px 14px}
.search-btn{right:4px;top:4px;width:30px;height:30px;border-radius:50%;background:var(--red)}
.brand{left:0;width:1200px;top:20px;text-align:center}
.brand-name{font-family:"Russo One",sans-serif;font-size:30px;color:var(--navy);letter-spacing:1px;line-height:1;white-space:nowrap}
.brand-url{font-size:11px;color:#333;margin-top:2px}
.callus{left:897px;top:16px;width:300px}
.callus .ring{position:absolute;left:0;top:2px;width:40px;height:40px;border:2px solid var(--red);border-radius:50%}
.callus .lbl{position:absolute;left:51px;top:2px;font-size:14px;color:#333}
.callus .num{position:absolute;left:51px;top:19px;font-size:22px;font-weight:700;color:var(--red)}
.nav{top:76px;left:0;width:1200px;height:42px;background:var(--navy);display:flex;justify-content:center;align-items:center}
.nav a{color:var(--white);text-decoration:none;font-size:14.5px;font-weight:500;padding:0 36px;position:relative}
.nav a+a::before{content:"|";position:absolute;left:-2px;color:#cfdbe4}
.nav a.active{color:#e3262f}
.nav a.active::after{content:"";position:absolute;left:36px;right:36px;bottom:-8px;height:2px;background:var(--red)}

/* hero */
.hero{top:118px;left:0;width:1200px;height:556px;background:linear-gradient(100deg,#6d5d4f 0%,#806d5a 35%,#8a7862 55%,#6f6750 75%,#5e5a48 100%)}
.hero-title{left:134px;top:272px;font-size:44px;color:var(--white);letter-spacing:1px}
.hero-text{left:136px;top:348px;width:410px;font-size:17px;line-height:28px;color:var(--white);font-weight:500}
.btn-red{background:var(--red);color:var(--white);font-weight:700;font-size:16px;border-radius:27px;display:flex;align-items:center;justify-content:center;gap:8px}
.hero-btn{left:136px;top:425px;width:195px;height:52px}
.arrow-ring{width:42px;height:42px;border:2px solid var(--white);border-radius:50%;display:flex;align-items:center;justify-content:center}

/* welcome */
.welcome-kicker{left:112px;top:755px;font-size:21px;font-weight:500;color:#111}
.welcome-title{left:112px;top:782px;font-size:42px;color:var(--navy)}
.welcome-title span{color:var(--red)}
.welcome-text{left:114px;top:852px;width:470px;font-size:15.5px;line-height:28.5px;color:var(--muted);text-align:justify}
.welcome-btn{left:115px;top:1060px;width:172px;height:48px;font-size:15px}
.welcome-photo{left:657px;top:734px;width:400px;height:400px;border-radius:50%;background:radial-gradient(circle at 50% 45%,#5b6066 0%,#2f3338 55%,#1b1d21 100%)}

/* features */
.features{top:1230px;left:0;width:1200px;height:134px;background:var(--navy)}
.feature{top:0;width:330px;height:134px}
.feature .badge{position:absolute;left:0;top:17px;width:100px;height:100px;border-radius:50%;background:var(--white);border:4px dashed var(--navy);outline:3px solid var(--white);display:flex;align-items:center;justify-content:center}
.feature h3{position:absolute;left:109px;top:32px;font-size:18px;font-weight:700;color:var(--white)}
.feature p{position:absolute;left:109px;top:60px;width:210px;font-size:15px;line-height:20px;color:var(--white)}

/* products */
.products{top:1363px;left:0;width:1200px;height:600px;background:var(--grey)}
.section-title{left:0;width:1200px;text-align:center;font-size:40px;color:var(--navy)}
.section-title span{color:var(--red)}
.products-sub{top:116px;left:0;width:1200px;text-align:center;font-size:15px;color:#333}
.card{top:179px;width:233px;height:325px;background:var(--white)}
.card .pic{position:absolute;left:26px;top:18px;width:181px;height:140px;border-radius:6px}
.card .stars{position:absolute;left:46px;top:188px;font-size:13px;color:var(--gold);letter-spacing:1px}
.card .reviews{position:absolute;left:138px;top:189px;font-size:13px;color:#444}
.card .name{position:absolute;left:0;width:233px;top:205px;text-align:center;font-size:17px;font-weight:500}
.card .price{position:absolute;left:0;width:233px;top:235px;text-align:center;font-size:13px;color:#333}
.card .price b{font-size:17px;color:var(--green);font-weight:500}
.card .qv{position:absolute;left:46px;top:265px;width:142px;height:38px;border-radius:19px;background:#111;color:var(--white);font-size:14px;font-weight:700;display:flex;align-items:center;justify-content:center}

/* split */
.split{top:1963px;left:0;width:1200px;height:389px}
.split-col{top:0;width:500px;text-align:center;color:var(--white)}
.split-col .emblem{margin:22px auto 0;width:100px;height:100px;border-radius:50%;border:4px dashed var(--white);display:flex;align-items:center;justify-content:center}
.split-col .emblem i{display:block;width:68px;height:68px;border-radius:50%;background:rgba(255,255,255,.92)}
.split-col h3{margin-top:24px;font-size:19px;font-weight:700;line-height:27px}
.split-col p{margin:18px auto 0;width:360px;font-size:15.5px;line-height:23px}
.btn-ghost{margin:24px auto 0;width:178px;height:52px;border:2px solid var(--white);border-radius:26px;display:flex;align-items:center;justify-content:center;gap:8px;font-weight:700;font-size:15px}
.seal{left:534px;top:2096px;width:132px;height:132px;border-radius:50%;background:var(--white);display:flex;align-items:center;justify-content:center}
.seal span{font-family:"Roboto",sans-serif;font-weight:700;font-size:15px;color:var(--navy);text-align:center;line-height:18px}

/* blog */
.post{top:2533px;width:296px;height:430px;background:var(--white);box-shadow:0 0 6px rgba(0,0,0,.18)}
.post .pic{position:absolute;left:0;top:0;width:296px;height:220px}
.post h4{position:absolute;left:0;width:296px;top:244px;text-align:center;font-size:19.5px;font-weight:500}
.post p{position:absolute;left:14px;width:268px;top:285px;text-align:center;font-size:13.5px;line-height:25.5px;color:var(--muted)}
.post .meta{position:absolute;left:0;width:296px;top:388px;text-align:center;font-size:13.5px;color:#444}

/* testimonials */
.testi{top:3085px;left:0;width:1200px;height:320px;background:var(--red)}
.testi-title{left:0;width:1200px;top:3148px;text-align:center;font-size:38px;color:var(--white);letter-spacing:1px}
.avatar{left:236px;top:3208px;width:108px;height:108px;border-radius:50%;background:linear-gradient(160deg,#8fb6dc,#3d6f9f);border:4px solid rgba(255,255,255,.8)}
.quote-mark{font-family:Georgia,serif;font-size:64px;color:var(--white);line-height:1}
.quote{left:406px;top:3219px;width:555px;font-size:16px;font-style:italic;line-height:23px;color:var(--white)}
.quote-name{left:406px;top:3310px;font-size:17px;font-weight:500;color:var(--white)}
.quote-co{left:406px;top:3335px;font-size:12px;color:var(--white)}
.round-arrow{width:36px;height:36px;border-radius:50%;background:var(--white);display:flex;align-items:center;justify-content:center}

/* footer */
.footer{top:3404px;left:0;width:1200px;height:401px;background:var(--dark);color:var(--white)}
.foot-brand{left:100px;top:3532px;width:224px;text-align:center}
.foot-brand .brand-name{color:#c9d3db;font-size:24px}
.foot-brand .brand-url{color:#aaa}
.socials{left:112px;top:3597px;display:flex;gap:6px}
.socials i{display:block;width:36px;height:36px;border:2px solid var(--white);border-radius:50%}
.foot-col h5{font-size:19px;font-weight:500;margin-bottom:20px}
.foot-col ul{list-style:none}
.foot-col li{font-size:15px;height:33.5px;position:relative;padding-left:26px}
.foot-col li::before{content:"»";position:absolute;left:3px;top:-2px;font-size:15px}
.contact li{padding-left:30px;line-height:21px;height:auto;margin-bottom:12px}
.contact li::before{content:""}
.contact svg{position:absolute;left:2px;top:3px}
.foot-rule{left:103px;top:3745px;width:1006px;height:1px;background:#555}
.copyright{left:0;width:1200px;top:3766px;text-align:center;font-size:15px}
</style>
</head>
<body>

<!-- Header -->
<header class="abs topbar">
  <div class="abs search">Search
    <span class="abs search-btn"><svg width="30" height="30" viewBox="0 0 30 30"><circle cx="14" cy="14" r="5.5" fill="none" stroke="#fff" stroke-width="2"/><line x1="18" y1="18" x2="21" y2="21" stroke="#fff" stroke-width="2.2"/></svg></span>
  </div>
  <div class="abs brand">
    <div class="brand-name">U.S. TORVANE</div>
    <div class="brand-url">ustorvane.com</div>
  </div>
  <div class="abs callus">
    <span class="ring"><svg width="36" height="36" viewBox="0 0 36 36"><path d="M12 10c1-1 2.4-1 3 0l2 3c.5 1 .2 1.8-.6 2.4l-1 .8c.8 2 2.4 3.7 4.4 4.6l.9-1c.6-.7 1.5-.9 2.4-.4l2.9 1.9c1 .6 1 2 .1 3l-1.4 1.4c-1.3 1.3-3.4 1.3-5.6.2-3.6-1.8-6.6-4.8-8.3-8.4-1.1-2.2-1-4.3.3-5.6z" fill="#a50d1e"/></svg></span>
    <span class="lbl">Call Us:</span>
    <span class="num">888-555-0142</span>
  </div>
</header>
<nav class="abs nav">
  <a class="active">HOME</a><a>ABOUT US</a><a>SERVICES</a><a>PRODUCTS</a><a>TESTIMONIALS</a><a>NEWS</a><a>CONTACT US</a>
</nav>

<!-- Hero -->
<section class="abs hero" role="img" aria-label="Photo of a soldier in camouflage aiming a rifle beside an all-terrain vehicle on muddy ground"></section>
<div class="abs display hero-title">U.S. TORVANE</div>
<p class="abs hero-text">Lorem ipsum dolor sit amet, consectetur adipiscing elit, sed do eiusmod tempor incididunt</p>
<div class="abs btn-red hero-btn">GET STARTED
  <svg width="16" height="16" viewBox="0 0 16 16"><circle cx="8" cy="8" r="7.5" fill="#fff"/><path d="M5 8h5M8 5l3 3-3 3" stroke="#a50d1e" stroke-width="1.8" fill="none"/></svg></div>
<div class="abs arrow-ring" style="left:32px;top:337px"><svg width="14" height="14" viewBox="0 0 14 14"><path d="M9 2 4 7l5 5" stroke="#fff" stroke-width="2" fill="none"/></svg></div>
<div class="abs arrow-ring" style="left:1129px;top:337px"><svg width="14" height="14" viewBox="0 0 14 14"><path d="M5 2l5 5-5 5" stroke="#fff" stroke-width="2" fill="none"/></svg></div>

<!-- Welcome -->
<div class="abs welcome-kicker">WELCOME TO</div>
<div class="abs display welcome-title"><span>U.S.</span> TORVANE</div>
<p class="abs welcome-text">Lorem ipsum dolor sit amet, consectetur adipiscing elit, sed do eiusmod tempor incididunt ut labore et dolore magna aliqua. Ut enim ad minim veniam, quis nostrud exercitation ullamco laboris nisi ut aliquip ex ea commodo consequat. Duis aute irure dolor in reprehenderit in voluptate velit esse cillum dolore eu fugiat nulla pariatur. Excepteur sint occaecat cupidatat non proident,</p>
<div class="abs btn-red welcome-btn">READ MORE
  <svg width="15" height="15" viewBox="0 0 16 16"><circle cx="8" cy="8" r="7.5" fill="#fff"/><path d="M5 8h5M8 5l3 3-3 3" stroke="#a50d1e" stroke-width="1.8" fill="none"/></svg></div>
<svg class="abs" style="left:650px;top:724px" width="430" height="420" viewBox="0 0 430 420" aria-hidden="true">
  <path d="M215 10 A200 200 0 0 1 215 410" fill="none" stroke="#1e4e6e" stroke-width="9" transform="translate(14 0)"/>
</svg>
<div class="abs welcome-photo" role="img" aria-label="Photo of masked police officers in black tactical gear"></div>

<!-- Features -->
<section class="abs features">
  <div class="abs feature" style="left:108px">
    <div class="badge"><svg width="50" height="50" viewBox="0 0 50 50"><circle cx="25" cy="20" r="14" fill="none" stroke="#1e4e6e" stroke-width="2.5"/><path d="M25 12l2.4 5 5.4.6-4 3.7 1.1 5.3L25 24l-4.9 2.6 1.1-5.3-4-3.7 5.4-.6z" fill="none" stroke="#1e4e6e" stroke-width="2"/><path d="M17 31l-4 13 6-3 3 5 3-9M33 31l4 13-6-3-3 5-3-9" fill="none" stroke="#1e4e6e" stroke-width="2"/></svg></div>
    <h3>QUALITY</h3>
    <p>Lorem ipsum dolor sit amet, consectetur &nbsp;elit, sed</p>
  </div>
  <div class="abs feature" style="left:446px">
    <div class="badge"><svg width="50" height="50" viewBox="0 0 50 50"><circle cx="25" cy="25" r="18" fill="none" stroke="#1e4e6e" stroke-width="2.5"/><path d="M14 34l16-16M20 16l14 14M12 38h26" stroke="#1e4e6e" stroke-width="2.5" fill="none"/></svg></div>
    <h3>DURABILITY</h3>
    <p>Lorem ipsum dolor sit amet, consectetur &nbsp;elit, sed</p>
  </div>
  <div class="abs feature" style="left:785px">
    <div class="badge"><svg width="50" height="50" viewBox="0 0 50 50"><rect x="8" y="20" width="8" height="20" fill="none" stroke="#1e4e6e" stroke-width="2.5"/><path d="M16 22l8-11c2-2 5 0 4 3l-2 6h11c2 0 3 2 2 4l-4 13c-.5 2-2 3-4 3H16" fill="none" stroke="#1e4e6e" stroke-width="2.5"/></svg></div>
    <h3>RELIABILITY</h3>
    <p>Lorem ipsum dolor sit amet, consectetur &nbsp;elit, sed</p>
  </div>
</section>

<!-- Products -->
<section class="abs products">
  <h2 class="abs display section-title" style="top:56px"><span>OUR</span> PRODUCT</h2>
  <p class="abs products-sub">Lorem ipsum dolor sit amet, consectetur adipiscing elit, sed do eiusmod tempor incididunt</p>

  <div class="abs card" style="left:111px">
    <div class="pic" role="img" aria-label="Photo of a camouflage tactical backpack" style="background:radial-gradient(circle,#8a7a55 0%,#a89a78 55%,#fff 80%)"></div>
    <span class="stars">★★★★★</span><span class="reviews">5Reviws</span>
    <div class="name">Product Name</div>
    <div class="price">From <b>$22.90</b></div>
    <div class="qv">QUICK VIEW</div>
  </div>
  <div class="abs card" style="left:359px">
    <div class="pic" role="img" aria-label="Photo of a military-style belt" style="background:radial-gradient(ellipse,#57503c 0%,#8a8470 45%,#fff 75%)"></div>
    <span class="stars">★★★★★</span><span class="reviews">5Reviws</span>
    <div class="name">Product Name</div>
    <div class="price">From <b>$22.90</b></div>
    <div class="qv">QUICK VIEW</div>
  </div>
  <div class="abs card" style="left:607px">
    <div class="pic" role="img" aria-label="Photo of a black tactical flashlight" style="background:radial-gradient(ellipse,#1a1a1a 0%,#555 40%,#fff 72%)"></div>
    <span class="stars">★★★★★</span><span class="reviews">5Reviws</span>
    <div class="name">Product Name</div>
    <div class="price">From <b>$22.90</b></div>
    <div class="qv">QUICK VIEW</div>
  </div>
  <div class="abs card" style="left:855px">
    <div class="pic" role="img" aria-label="Photo of an olive canteen pouch" style="background:radial-gradient(circle,#5f6a3a 0%,#8d9566 50%,#fff 78%)"></div>
    <span class="stars">★★★★★</span><span class="reviews">5Reviws</span>
    <div class="name">Product Name</div>
    <div class="price">From <b>$22.90</b></div>
    <div class="qv">QUICK VIEW</div>
  </div>
</section>

<!-- Split: military / law enforcement -->
<svg class="abs" style="left:0;top:1963px" width="1200" height="389" viewBox="0 0 1200 389" aria-hidden="true">
  <polygon points="0,0 628,0 566,389 0,389" fill="#a50d1e"/>
  <polygon points="640,0 1200,0 1200,389 578,389" fill="#1e4e6e"/>
</svg>
<section class="abs split">
  <div class="abs split-col" style="left:55px">
    <div class="emblem"><i></i></div>
    <h3>QUALITY TACTICAL EQUIPMENT<br>TO MILITARY</h3>
    <p>Lorem ipsum dolor sit amet, consectetur adipiscing elit, sed do eiusmod tempor incididunt ut labore et dolore magna aliqua.</p>
    <div class="btn-ghost">READ MORE <svg width="15" height="15" viewBox="0 0 16 16"><circle cx="8" cy="8" r="7.5" fill="#fff"/><path d="M5 8h5M8 5l3 3-3 3" stroke="#a50d1e" stroke-width="1.8" fill="none"/></svg></div>
  </div>
  <div class="abs split-col" style="left:628px">
    <div class="emblem"><i></i></div>
    <h3>QUALITY TACTICAL EQUIPMENT<br>TO LAW ENFORCEMENT</h3>
    <p>Lorem ipsum dolor sit amet, consectetur adipiscing elit, sed do eiusmod tempor incididunt ut labore et dolore magna aliqua.</p>
    <div class="btn-ghost">READ MORE <svg width="15" height="15" viewBox="0 0 16 16"><circle cx="8" cy="8" r="7.5" fill="#fff"/><path d="M5 8h5M8 5l3 3-3 3" stroke="#1e4e6e" stroke-width="1.8" fill="none"/></svg></div>
  </div>
</section>
<svg class="abs" style="left:524px;top:2086px" width="152" height="152" viewBox="0 0 152 152" aria-hidden="true">
  <circle cx="76" cy="76" r="72" fill="none" stroke="#fff" stroke-width="3" stroke-dasharray="6 5"/>
</svg>
<div class="abs seal"><span>U.S.<br>TORVANE</span></div>

<!-- Blog -->
<h2 class="abs display section-title" style="top:2455px"><span>OUR</span> BLOG</h2>
<article class="abs post" style="left:121px">
  <div class="pic" role="img" aria-label="Photo of soldiers on a sandy hill at sunset" style="background:linear-gradient(180deg,#c9b28a,#a88a5e 60%,#6e5a3d)"></div>
  <h4>Sed ut perspiciatis unde</h4>
  <p>Nemo enim ipsam voluptatem quia voluptas sit aspernatur aut odit aut fugit, sed quia con ratione voluptatem sequi nesciunt.</p>
  <div class="meta">◉ By Dean Corwell &nbsp;&nbsp;| &nbsp;&nbsp;▣ June 18, 2020</div>
</article>
<article class="abs post" style="left:453px">
  <div class="pic" role="img" aria-label="Photo of tactical gear laid out flat: vest, helmet, rifle and boots" style="background:linear-gradient(135deg,#9c8f70,#6e6650 50%,#a79a7b)"></div>
  <h4>Sed ut perspiciatis unde</h4>
  <p>Nemo enim ipsam voluptatem quia voluptas sit aspernatur aut odit aut fugit, sed quia con ratione voluptatem sequi nesciunt.</p>
  <div class="meta">◉ By Dean Corwell &nbsp;&nbsp;| &nbsp;&nbsp;▣ June 18, 2020</div>
</article>
<article class="abs post" style="left:785px">
  <div class="pic" role="img" aria-label="Photo of masked officers in black uniforms walking" style="background:linear-gradient(180deg,#b9bcbf,#4a4d52 55%,#26282c)"></div>
  <h4>Sed ut perspiciatis unde</h4>
  <p>Nemo enim ipsam voluptatem quia voluptas sit aspernatur aut odit aut fugit, sed quia con ratione voluptatem sequi nesciunt.</p>
  <div class="meta">◉ By Dean Corwell &nbsp;&nbsp;| &nbsp;&nbsp;▣ June 18, 2020</div>
</article>

<!-- Testimonials -->
<section class="abs testi"></section>
<h2 class="abs display testi-title">TESTIMONIALS</h2>
<div class="abs round-arrow" style="left:111px;top:3236px"><svg width="16" height="12" viewBox="0 0 16 12"><path d="M15 6H2M6 1 1 6l5 5" stroke="#222" stroke-width="2" fill="none"/></svg></div>
<div class="abs round-arrow" style="left:1052px;top:3236px"><svg width="16" height="12" viewBox="0 0 16 12"><path d="M1 6h13M10 1l5 5-5 5" stroke="#222" stroke-width="2" fill="none"/></svg></div>
<div class="abs avatar" role="img" aria-label="Portrait photo of the customer"></div>
<div class="abs quote-mark" style="left:355px;top:3192px">&ldquo;</div>
<p class="abs quote">Lorem ipsum dolor sit amet, consectetur adipiscing elit, sed do eiusmod tempor incididunt ut labore et dolore magna aliqua. Ut enim ad minim veniam, quis nostrud exercitation ullamco laboris nisi ut aliquip ex ea commodo consequat.</p>
<div class="abs quote-mark" style="left:896px;top:3292px">&rdquo;</div>
<div class="abs quote-name">Mark Halden</div>
<div class="abs quote-co">Company Name</div>

<!-- Footer -->
<footer class="abs footer"></footer>
<div class="abs foot-brand">
  <div class="brand-name">U.S. TORVANE</div>
  <div class="brand-url">ustorvane.com</div>
</div>
<div class="abs socials"><i></i><i></i><i></i><i></i></div>
<div class="abs foot-col" style="left:375px;top:3481px;color:#fff">
  <h5>Company</h5>
  <ul><li>Home</li><li>Services</li><li>About</li><li>Products</li><li>Contact</li></ul>
</div>
<div class="abs foot-col" style="left:596px;top:3481px;color:#fff">
  <h5>Resources</h5>
  <ul><li>Blogs</li><li>News</li><li>Support</li><li>Links</li><li>Term of Use</li></ul>
</div>
<div class="abs foot-col contact" style="left:825px;top:3481px;width:280px;color:#fff">
  <h5>Contact us</h5>
  <ul>
    <li><svg width="12" height="14" viewBox="0 0 12 14"><path d="M6 0a5 5 0 0 1 5 5c0 4-5 9-5 9S1 9 1 5a5 5 0 0 1 5-5z" fill="#fff"/><circle cx="6" cy="5" r="2" fill="#1c1c1f"/></svg>123, Lorem ipsum dolor sit amet, consectetur elit,</li>
    <li><svg width="12" height="14" viewBox="0 0 12 14"><rect x="3" y="1" width="6" height="12" rx="1" fill="none" stroke="#fff" stroke-width="1.6"/></svg>(888) 555-0142</li>
    <li><svg width="14" height="14" viewBox="0 0 14 14"><rect x="1" y="4" width="12" height="9" fill="#fff"/><rect x="4" y="1" width="6" height="4" fill="none" stroke="#fff" stroke-width="1.4"/></svg>(123) 555-0199</li>
    <li><svg width="14" height="12" viewBox="0 0 14 12"><rect x="1" y="1" width="12" height="10" fill="none" stroke="#fff" stroke-width="1.5"/><path d="M1 1l6 5 6-5" fill="none" stroke="#fff" stroke-width="1.5"/></svg>info@ustorvane.com</li>
  </ul>
</div>
<div class="abs foot-rule"></div>
<div class="abs copyright" style="color:#fff">© 2020 U.S. Torvane | All Rights Reserved</div>

</body>
</html>
```